Business Card Design

We need a business card designed for our new company. Prefer a black card with white logo & writing.

Contact Information for Business Card

Ted Galloway, address: 7-4812 Fernhollow Road, Abbotsford, BC, V3K 8R2, Office Phone: 604-712-3390, Cell: 604-947-2164, Email: ted@resinworkshub.ca

Colors

Designer to choose only greyscale colors for use in the design.

```html
<!DOCTYPE html>
<html lang="en">
<head>
<meta charset="UTF-8">
<title>Resinworks Hub – Business Card</title>
<link href="https://fonts.googleapis.com/css2?family=Montserrat:wght@400;700&display=swap" rel="stylesheet">
<style>
  :root {
    --stage: #262626;
    --card-light: #ffffff;
    --card-dark: #000000;
    --ink: #111111;
    --ink-soft: #1a1a1a;
    --paper: #ffffff;
  }
  * { margin: 0; padding: 0; box-sizing: border-box; }
  html, body {
    width: 1200px; height: 900px; overflow: hidden;
    background: var(--stage);
    font-family: "Montserrat", Arial, sans-serif;
  }
  .canvas { position: relative; width: 1200px; height: 900px; }
  .card { position: absolute; left: 341px; width: 518px; height: 296px; }
  .card-front { top: 141px; background: var(--card-light); color: var(--ink); }
  .card-back { top: 463px; background: var(--card-dark); color: var(--paper); }

  .holder-name {
    position: absolute; right: 276px; top: 274px; transform: translateY(-50%);
    font-size: 25px; font-weight: 700; letter-spacing: 0.2px; white-space: nowrap;
  }
  .card-front .holder-name { top: 148px; }
  .divider {
    position: absolute; left: 259px; top: 115px; width: 2px; height: 66px;
    background: var(--ink);
  }
  .contact-list { position: absolute; left: 277px; top: 113px; list-style: none; }
  .contact-list li {
    display: flex; align-items: center; height: 18px;
    font-size: 14px; color: var(--ink-soft); white-space: nowrap;
  }
  .contact-list svg { width: 12px; height: 12px; margin-right: 6px; flex: none; }
  .address {
    position: absolute; left: 0; right: 0; top: 395px; top: 254px;
    text-align: center; font-size: 13.5px; color: var(--ink-soft);
  }

  .brand {
    position: absolute; inset: 0; display: flex; align-items: center; justify-content: center;
    font-size: 34px; font-weight: 700; letter-spacing: 1px; color: var(--paper);
  }
</style>
</head>
<body>
<main class="canvas">
  <section class="card card-front">
    <h1 class="holder-name">TED GALLOWAY</h1>
    <span class="divider"></span>
    <ul class="contact-list">
      <li>
        <svg viewBox="0 0 24 24" aria-hidden="true"><path fill="currentColor" d="M6.6 10.8a15.1 15.1 0 0 0 6.6 6.6l2.2-2.2a1 1 0 0 1 1-.25 11.4 11.4 0 0 0 3.6.57 1 1 0 0 1 1 1V20a1 1 0 0 1-1 1A17 17 0 0 1 3 4a1 1 0 0 1 1-1h3.5a1 1 0 0 1 1 1c0 1.25.2 2.45.57 3.57a1 1 0 0 1-.25 1z"/></svg>
        604-712-3390
      </li>
      <li>
        <svg viewBox="0 0 24 24" aria-hidden="true"><rect x="6" y="2" width="12" height="20" rx="2" fill="none" stroke="currentColor" stroke-width="2"/><circle cx="12" cy="18" r="1.2" fill="currentColor"/></svg>
        604-947-2164
      </li>
      <li>
        <svg viewBox="0 0 24 24" aria-hidden="true"><path fill="currentColor" d="M2 6h20v12H2z"/><path fill="none" stroke="#fff" stroke-width="1.6" d="M2.5 6.5 12 13l9.5-6.5"/></svg>
        ted@resinworkshub.ca
      </li>
      <li>
        <svg viewBox="0 0 24 24" aria-hidden="true"><g fill="none" stroke="currentColor" stroke-width="1.8"><circle cx="12" cy="12" r="9.5"/><ellipse cx="12" cy="12" rx="4" ry="9.5"/><path d="M2.5 12h19M4 7h16M4 17h16"/></g></svg>
        resinworkshub.ca
      </li>
    </ul>
    <p class="address">7-4812 Fernhollow Road, Abbotsford, BC, V3K 8R2</p>
  </section>

  <section class="card card-back">
    <p class="brand">RESINWORKS HUB</p>
  </section>
</main>
</body>
</html>
```